Business card for a Exhibition booth fabrication company

Hi. My company would like to change our corporate name card. We are an events and Exhibition stand builder company. We would like our corporate name card to resonate what we do. I need someone to create something unique that relates to the industry that I am in. The graphic designer should be creative to incorporate the elements of my industry and try to blend in well in the design of the card. Our aim is to ensure that we are unique and our card can look different from our competitors.
Updates

Target Market(s)

Marketing and events manager from all companies

Contact Information for Business Card

The business card should have the following details:
Name
Job Title
Email
Website

Colors

Designer to choose colors to be used in the design.

Requirements
Must have
• The card must be look something that is relevant to the service that I am providing. My website is: www.velmora-buildworks.com
• You can see my website to get more information on what service that I am doing
Nice to have
• On the back of my card, I would like to have a globe image with the incorporation of my company logo. This is to indicate that my services can be done in any part of the world.

```html
<!DOCTYPE html>
<html lang="en">
<head>
<meta charset="utf-8">
<title>Velmora Buildworks – Business Card</title>
<link href="https://fonts.googleapis.com/css2?family=Open+Sans:wght@400;600;700&family=Michroma&display=swap" rel="stylesheet">
<style>
  :root {
    --stage-light: #dcdddf;
    --stage-dark: #a3a4a7;
    --card-white: #ffffff;
    --brand-red: #ed1c24;
    --brand-grey: #616265;
    --text-grey: #58595b;
    --back-grey: #646567;
    --map-grey: #77787a;
    --light-text: #f2f2f2;
  }
  * { margin: 0; padding: 0; box-sizing: border-box; }
  html, body { width: 1200px; height: 1118px; overflow: hidden; }
  body {
    position: relative;
    background: linear-gradient(90deg, var(--stage-light) 0%, #c4c5c8 45%, var(--stage-dark) 100%);
    font-family: "Open Sans", Arial, sans-serif;
  }
  .card {
    position: absolute;
    width: 756px;
    height: 431px;
    overflow: hidden;
  }
  /* Front */
  .card-front { left: 115px; top: 99px; background: var(--card-white); }
  .brand {
    position: absolute; left: 38px; top: 130px;
    display: flex; align-items: center; gap: 14px;
  }
  .brand-square { width: 22px; height: 22px; background: var(--brand-red); }
  .brand-name {
    font-family: "Michroma", Arial, sans-serif;
    font-size: 23px; letter-spacing: 1.5px;
    color: var(--brand-grey);
  }
  .address {
    position: absolute; left: 36px; top: 243px;
    font-size: 17.5px; color: var(--text-grey);
  }
  .band { position: absolute; left: 0; top: 276px; width: 756px; height: 155px; }
  .contact-list { position: absolute; left: 35px; top: 311px; list-style: none; }
  .contact-list li {
    display: flex; align-items: center; gap: 12px;
    height: 34.5px; font-size: 18.5px; color: var(--card-white);
  }
  .contact-list svg { width: 20px; height: 20px; flex: none; }
  .nameplate {
    position: absolute; left: 413px; top: 270px; width: 267px; height: 63px;
    text-align: center; color: var(--card-white);
  }
  .person-name { padding-top: 6px; font-size: 23px; font-weight: 700; letter-spacing: 0.5px; font-family: Arial, "Open Sans", sans-serif; }
  .person-title { font-size: 17px; letter-spacing: 0.8px; font-family: Arial, "Open Sans", sans-serif; }
  /* Back */
  .card-back { left: 364px; top: 588px; background: var(--back-grey); }
  .world-map {
    position: absolute; left: 0; top: 60px; width: 756px; height: 300px;
    background: radial-gradient(ellipse at 50% 45%, var(--map-grey) 0%, rgba(119,120,122,0.55) 55%, rgba(100,101,103,0) 80%);
  }
  .back-brand {
    position: absolute; left: 0; right: 0; top: 178px;
    display: flex; justify-content: center; align-items: center; gap: 16px;
  }
  .back-brand .brand-square { background: #d8d8d8; width: 26px; height: 26px; }
  .back-brand .brand-name { color: #e6e6e6; font-size: 30px; }
  .back-web {
    position: absolute; left: 0; right: 0; top: 390px;
    text-align: center; font-size: 20px; letter-spacing: 4px; color: var(--light-text);
  }
</style>
</head>
<body>
  <section class="card card-front" aria-label="Business card front">
    <div class="brand">
      <span class="brand-square"></span>
      <span class="brand-name">VELMORA BUILDWORKS</span>
    </div>
    <p class="address">Street Name, City Name, Zipcode - 01234</p>
    <svg class="band" viewBox="0 0 756 155" preserveAspectRatio="none" aria-hidden="true">
      <path d="M0 0 H395 C408 0 412 8 414 20 C418 50 430 57 455 57 H650 C675 57 688 48 690 20 C692 6 700 0 712 0 H756 V155 H0 Z" fill="var(--brand-red)"/>
      <path d="M398 -6 H686 C700 -6 706 4 706 14 V28 C706 46 694 57 676 57 H436 C418 57 406 46 406 28 V8 C406 0 398 -6 398 -6 Z" fill="var(--brand-grey)"/>
    </svg>
    <div class="nameplate">
      <div class="person-name">DANIEL HARWICK</div>
      <div class="person-title">PRESIDENT</div>
    </div>
    <ul class="contact-list">
      <li>
        <svg viewBox="0 0 24 24" aria-hidden="true"><path fill="#fff" d="M6.6 3.5l3 3.2-1.8 2.2c1.2 2.5 3.1 4.5 5.5 5.8l2.2-1.9 3.2 3-2 3.1C10.5 18.6 5.4 13.4 3.5 5.6z"/></svg>
        012-345-6789
      </li>
      <li>
        <svg viewBox="0 0 24 24" aria-hidden="true"><rect x="2" y="5" width="20" height="14" fill="#fff"/><path d="M2.5 5.5 12 13l9.5-7.5M2.5 18.5l7-6.5M21.5 18.5l-7-6.5" stroke="var(--brand-red)" stroke-width="1.6" fill="none"/></svg>
        info@velmora-buildworks.com
      </li>
      <li>
        <svg viewBox="0 0 24 24" aria-hidden="true"><g fill="none" stroke="#fff" stroke-width="1.8"><circle cx="12" cy="12" r="9.5"/><ellipse cx="12" cy="12" rx="4.2" ry="9.5"/><path d="M2.5 12h19M4 7h16M4 17h16"/></g></svg>
        www.velmora-buildworks.com
      </li>
    </ul>
  </section>

  <section class="card card-back" aria-label="Business card back">
    <div class="world-map" role="img" aria-label="Faint world map spanning the card"></div>
    <div class="back-brand">
      <span class="brand-square"></span>
      <span class="brand-name">VELMORA BUILDWORKS</span>
    </div>
    <p class="back-web">www.velmora-buildworks.com</p>
  </section>
</body>
</html>
```